Accountability Project Graphics

I want to create 10 social media graphics (new Instagram size 4:5 (1080 x 1350 pixels) focusing on our Quilvo Accountability App, using any of the 3 pictures attached. Use the attached pics only, NO RANDOM STOCK PHOTOGRAPHY. For the color scheme, use the landing page colors/fonts (attached).
You can add any of the 3 photos attached but I mainly need BOLD text that includes these headlines and sub-headlines on them.
Please NOTE for all the headlines below, also add this sub-headline on each graphic:
Stay Consistent with RT in Your Pocket!
Here are the headlines:
• Stop Starting Over Every Monday
• You don't need more willpower. You need more support
• Built for women who are tired of doing this alone
• When Motivation Fades, RT Checks In
• The Support System You've Been Missing
• Support When Motivation Disappears
• What if RT Checked in Every Day?
• The Missing Piece Isn't Another Diet
• Eat the food you love. Stay accountable every day.
• One Bad Meal Doesn't Mean You Failed
women over 40 trying to lose weight

```html
<!DOCTYPE html>
<html lang="en">
<head>
<meta charset="utf-8">
<title>Quilvo Accountability – Social Graphics</title>
<link rel="stylesheet" href="https://fonts.googleapis.com/css2?family=Source+Serif+4:opsz,wght@8..60,700&family=Oswald:wght@700&family=Mulish:wght@700;800&display=swap">
<style>
  :root{
    --stage:#a3a3a3;
    --plum:#2a0b3a;
    --purple:#3d1050;
    --purple-deep:#260a33;
    --pink:#e0195f;
    --rose:#d43c6f;
    --blush:#fde7ed;
    --blush-2:#fbd6e1;
    --white:#ffffff;
  }
  *{box-sizing:border-box;margin:0;padding:0}
  html,body{width:1200px;height:410px;overflow:hidden;background:var(--stage)}
  .board{position:relative;width:1200px;height:410px}
  .post{position:absolute;top:51px;width:247px;height:308px;overflow:hidden}
  .photo{position:absolute}

  .pill{position:absolute;display:flex;align-items:center;gap:5px;padding:0 6px;
        background:var(--plum);color:var(--white);border-radius:12px;
        font-family:"Mulish",sans-serif;font-weight:800;font-size:5.6px;line-height:1.45}
  .pill .dot{flex:none;width:11px;height:11px;border-radius:50%;background:var(--white);display:flex;align-items:center;justify-content:center}
  .pill .dot svg{width:7px;height:7px}
  .pill em{font-style:normal;color:var(--pink)}

  .rule{position:absolute;height:2px;border-radius:1px}

  /* Post 1 */
  .post--monday{left:53px;background:linear-gradient(135deg,var(--white),var(--blush) 60%,var(--blush-2));border:1px solid var(--rose)}
  .post--monday .photo{left:122px;top:18px;width:125px;height:290px;
        background:linear-gradient(180deg,#5a3a3a 0%,#1d1418 35%,#141014 100%);border-radius:60px 60px 0 0}
  .serif-stack{position:absolute;left:4px;top:42px;width:112px;text-align:center;
        font-family:"Source Serif 4",serif;font-weight:700;color:var(--plum);line-height:.98}
  .serif-stack .big{font-size:47px;display:block;text-align:left;padding-left:4px}
  .serif-stack .line{font-size:28px;display:block}
  .serif-stack .accent{color:var(--rose)}
  .post--monday .rule{left:12px;top:213px;width:88px;background:var(--rose)}
  .post--monday .pill{left:14px;top:231px;width:89px;height:22px}

  /* Post 2 */
  .post--support{left:335px;background:radial-gradient(circle at 85% 10%,#b5489e 0%,#6a1f70 30%,var(--purple) 60%,var(--purple-deep) 100%)}
  .post--support .photo{left:102px;top:80px;width:145px;height:228px;
        background:linear-gradient(160deg,#1a1016 0%,#3b1d24 40%,#d9d98a 75%,#ec4f93 100%);border-radius:50px 50px 0 0}
  .quote{position:absolute;left:7px;top:29px;width:100px;text-align:center;
        font-family:"Source Serif 4",serif;font-weight:700;color:var(--white);font-size:18.5px;line-height:22.4px}
  .quote span{display:block;white-space:nowrap}
  .post--support .bracket{position:absolute;left:8px;top:18px}
  .post--support .pill{left:14px;top:259px;width:89px;height:22px;background:transparent;border:1px solid var(--white)}

  /* Post 3 */
  .post--fades{left:618px;background:linear-gradient(180deg,#3a0e4c,var(--purple-deep))}
  .side-band{position:absolute;left:0;top:0;width:30px;height:308px;background:var(--pink)}
  .side-band span{position:absolute;left:50%;top:50%;transform:translate(-50%,-50%) rotate(-90deg);white-space:nowrap;
        font-family:"Oswald",sans-serif;font-weight:700;font-size:17px;color:var(--white)}
  .post--fades .photo{left:146px;top:66px;width:101px;height:242px;
        background:linear-gradient(180deg,#4a3030 0%,#1b1218 30%,#120e12 100%);border-radius:45px 45px 0 0}
  .bold-head{position:absolute;left:38px;top:66px;font-family:"Oswald",sans-serif;font-weight:700;
        color:var(--white);font-size:27px;line-height:31px}
  .post--fades .rule{left:38px;top:174px;width:85px;background:var(--pink)}
  .post--fades .checks{position:absolute;left:38px;top:192px;font-family:"Oswald",sans-serif;font-weight:700;color:var(--pink);font-size:24px;line-height:30px}

  /* Post 4 */
  .post--daily{left:901px;background:linear-gradient(180deg,var(--blush),#fff 60%,var(--blush));border:1px solid var(--rose)}
  .daily-title{position:absolute;left:0;top:9px;width:100%;text-align:center;font-family:"Oswald",sans-serif;
        font-weight:700;color:var(--plum);font-size:25px;line-height:23px}
  .daily-title .accent{color:var(--pink)}
  .post--daily .pill{left:41px;top:61px;width:164px;height:16px;gap:5px;font-size:6.6px;white-space:nowrap}
  .post--daily .pill .dot{width:9px;height:9px}
  .post--daily .ring{position:absolute;left:0;top:0}
  .post--daily .photo{left:36px;top:98px;width:176px;height:210px;
        background:linear-gradient(180deg,#2b2430 0%,#2d3e63 45%,#e8e6e4 60%,#32466f 100%);border-radius:60px 60px 0 0}
</style>
</head>
<body>
<div class="board">

  <section class="post post--monday">
    <div class="photo" role="img" aria-label="Smiling woman in a black lace top posing with hand on hip, pink brush stroke behind"></div>
    <h2 class="serif-stack">
      <span class="big">Stop</span>
      <span class="line accent">Starting</span>
      <span class="line">Over</span>
      <span class="line">Every</span>
      <span class="line accent">Monday</span>
    </h2>
    <div class="rule"></div>
    <div class="pill"><span class="dot"><svg viewBox="0 0 10 10"><path d="M5 9 L1.2 5 A2.2 2.2 0 0 1 5 2.3 A2.2 2.2 0 0 1 8.8 5 Z" fill="var(--pink)"/></svg></span><span>Stay Consistent with<br><em>RT</em> in Your Pocket!</span></div>
  </section>

  <section class="post post--support">
    <div class="photo" role="img" aria-label="Two women sharing a joyful hug against soft purple bokeh lights"></div>
    <svg class="bracket" width="200" height="235" viewBox="0 0 200 235">
      <path d="M0 40 V0 H46" stroke="var(--pink)" stroke-width="1" fill="none"/>
      <path d="M97 193 V231 H58" stroke="var(--pink)" stroke-width="1" fill="none"/>
    </svg>
    <h2 class="quote"><span>You</span><span>don’t</span><span>need</span><span>more</span><span>willpower</span><span>You</span><span>need</span><span>more</span><span>support</span></h2>
    <div class="pill"><span class="dot"><svg viewBox="0 0 10 10"><path d="M5 9 L1.2 5 A2.2 2.2 0 0 1 5 2.3 A2.2 2.2 0 0 1 8.8 5 Z" fill="var(--pink)"/></svg></span><span>Stay Consistent with<br><em>RT</em> in Your Pocket!</span></div>
  </section>

  <section class="post post--fades">
    <div class="side-band"><span>Stay Consistent with RT in Your Pocket!</span></div>
    <div class="photo" role="img" aria-label="Smiling woman in a black lace top with hand on hip, purple brush stroke behind"></div>
    <h2 class="bold-head">When<br>Motivation<br>Fades,</h2>
    <div class="rule"></div>
    <p class="checks">RT Checks In</p>
  </section>

  <section class="post post--daily">
    <h2 class="daily-title">What if RT Checked in<br><span class="accent">Every Day?</span></h2>
    <div class="pill"><span class="dot"><svg viewBox="0 0 10 10"><path d="M5 9 L1.2 5 A2.2 2.2 0 0 1 5 2.3 A2.2 2.2 0 0 1 8.8 5 Z" fill="var(--pink)"/></svg></span><span>Stay Consistent with <em>RT</em> in Your Pocket!</span></div>
    <svg class="ring" width="247" height="308" viewBox="0 0 247 308">
      <circle cx="135" cy="154" r="66" fill="#fbd3df"/>
      <circle cx="135" cy="154" r="58" fill="#f3eef2"/>
    </svg>
    <div class="photo" role="img" aria-label="Two women laughing together on stage, one holding a microphone"></div>
  </section>

</div>
</body>
</html>
```